Brightmoor Lift Inc Website Deisgn

We are a new small elevator contracting company.
We would like a full website designed similar to
http://pellingtonlifts.com or https://www.northvalelifting.ca/
In addition to contents found on the above webpages.. we would like a section for project gallery etc.... have fun with it ... make it professional

Target Market(s)

Elevator Consultants - Property managers - Condo Boards - Commercial office buildings

Coding

Number of Pages Required

5+ page

Requirements
Must have
• Navigation Bar.. Be view able via mobile ..Should be pictures of Tall Office buildings in background.. Toronto city skyline etc....

Have Fun!

```html
<!DOCTYPE html>
<html lang="en">
<head>
<meta charset="utf-8">
<title>Brightmoor Lift Inc</title>
<link href="https://fonts.googleapis.com/css2?family=Roboto+Condensed:wght@400;700&family=Roboto:wght@400;500;700&display=swap" rel="stylesheet">
<style>
:root{
  --blue:#1c5bb4;
  --blue-deep:#134a98;
  --ink:#1d1d1f;
  --text:#555a60;
  --muted:#8a8f96;
  --card:#efefef;
  --dark:#16181c;
  --white:#ffffff;
  --line:#e2e4e8;
}
*{margin:0;padding:0;box-sizing:border-box}
html,body{width:1200px;height:3984px;overflow:hidden;background:var(--white)}
body{position:relative;font-family:"Roboto",Arial,sans-serif;color:var(--ink)}
.abs{position:absolute}
.cond{font-family:"Roboto Condensed","Arial Narrow",sans-serif}

/* hero */
.hero{left:0;top:0;width:1200px;height:780px;background:linear-gradient(160deg,#dfe9f5 0%,#9fbde0 35%,#5f8dc6 70%,#3b6eb2 100%)}
.hero-svg{left:0;top:560px}
.brand{font-family:"Roboto Condensed",sans-serif;font-weight:700;color:var(--ink);white-space:nowrap}
.brand-top{left:144px;top:26px;font-size:24px;line-height:1;display:flex;align-items:center;gap:8px}
.brand-dot{width:18px;height:18px;border-radius:50%;background:var(--ink)}
.nav{left:448px;top:30px;display:flex;gap:22px;font-size:17px;font-weight:500;white-space:nowrap}
.nav a{color:var(--ink);text-decoration:none;position:relative}
.nav a.active{color:var(--blue)}
.nav a.active::after{content:"";position:absolute;left:0;right:0;bottom:-10px;height:3px;background:var(--blue)}
.phone{left:834px;top:20px;display:flex;align-items:center;gap:8px;font-family:"Roboto Condensed",sans-serif;font-weight:700;font-size:28px;white-space:nowrap}
.hero-title{left:0;width:1200px;top:240px;text-align:center;font-size:66px;color:var(--ink)}
.tagline{left:0;width:1200px;top:362px;text-align:center;font-size:25px;color:var(--ink)}
.btn{display:flex;align-items:center;justify-content:center;gap:8px;background:var(--blue);color:var(--white);font-family:"Roboto Condensed",sans-serif;font-weight:700;border-radius:40px;white-space:nowrap}
.btn-hero{left:484px;top:436px;width:233px;height:59px;font-size:19px}
.dots{left:556px;top:563px;display:flex;gap:8px}
.dots span{width:11px;height:11px;border-radius:50%;background:var(--white)}
.dots span.on{background:var(--blue)}

/* about */
.about-ring{left:151px;top:788px;width:372px;height:372px;border-radius:50%;background:var(--white);box-shadow:0 0 14px rgba(0,0,0,.2)}
.about-photo{left:163px;top:800px;width:348px;height:348px;border-radius:50%;background:linear-gradient(180deg,#8fc3ee,#3d6fa8 60%,#23354f)}
.about-inner{left:200px;top:837px;width:274px;height:274px;border-radius:50%;border:12px solid var(--white)}
.about-h1{left:614px;top:784px;font-size:48px;font-weight:700;color:var(--blue)}
.about-h2{left:614px;top:842px;font-size:50px;font-weight:700}
.about-h3{left:614px;top:898px;font-size:38px;letter-spacing:10px}
.about-p{left:614px;top:962px;width:452px;font-size:13.5px;line-height:27.5px;color:var(--text);z-index:2}

/* services */
.services-band{left:0;top:1150px;width:1200px;height:550px;background:linear-gradient(180deg,#1c5bb4,#2a68bf 60%,#1f5aae)}
.services-svg{left:0;top:1150px}
.section-title{left:0;width:1200px;text-align:center;font-family:"Roboto Condensed",sans-serif;font-weight:700;font-size:50px}
.services-title{top:1380px;color:var(--white)}
.card{width:293px;height:427px;top:1510px;background:var(--card);border-top:14px solid var(--white);border-left:14px solid var(--white);border-right:14px solid var(--white);border-bottom:none;text-align:center}
.card-img{width:265px;height:175px;margin:0 auto}
.card h3{font-size:19px;font-weight:700;margin-top:36px}
.card p{font-size:14px;line-height:23px;color:var(--text);margin:12px auto 0;width:230px}
.card .btn{width:136px;height:40px;font-size:14.5px;margin:22px auto 0}

/* gallery */
.gallery-title{top:2045px}
.gallery-title span{color:var(--blue)}

/* quote */
.quote-band{left:0;top:2870px;width:1200px;height:750px;background:linear-gradient(180deg,#2b2f36,#101215 45%,#1c1f24)}
.quote-svg{left:0;top:2868px}
.quote-title{top:3100px;color:var(--white)}
.quote-title span{color:var(--blue)}
.field{background:var(--white);border:1px solid #cfd3d8;font-size:14.5px;color:var(--muted);padding:14px 20px}
.btn-submit{left:464px;top:3460px;width:272px;height:57px;font-size:19px}

/* contact */
.contact{width:300px;text-align:center}
.c-icon{width:72px;height:72px;border-radius:50%;border:2px solid #7d8490;margin:0 auto;display:flex;align-items:center;justify-content:center}
.c-icon.fill{background:var(--blue);border-color:var(--blue)}
.contact h4{font-size:15px;font-weight:500;margin-top:20px}
.contact p{font-size:12.5px;line-height:22px;color:var(--text);margin-top:6px}
.rule{left:0;top:3873px;width:1200px;height:1px;background:var(--line)}
.copy{left:144px;top:3920px;font-size:11.5px;color:var(--text)}
.social{top:3907px;width:40px;height:40px;border-radius:50%;border:2px solid var(--blue)}
.foot-bar{left:0;top:3973px;width:1200px;height:11px;background:var(--blue)}
</style>
</head>
<body>

<!-- hero -->
<div class="abs hero" role="img" aria-label="Upward view of tall glass office towers in blue tones"></div>
<svg class="abs hero-svg" width="1200" height="220" viewBox="0 0 1200 220">
  <path d="M0 120 Q560 -20 1200 110 L1200 220 L0 220Z" fill="#1c5bb4"/>
  <path d="M0 195 Q560 50 1200 200" fill="none" stroke="#2b2e33" stroke-width="16"/>
  <path d="M0 222 Q560 90 1200 222Z" fill="#ffffff"/>
</svg>
<div class="abs brand brand-top"><span class="brand-dot"></span>BRIGHTMOOR LIFT INC</div>
<nav class="abs nav">
  <a class="active" href="#">Home</a><a href="#">About Us</a><a href="#">Services</a><a href="#">Blog</a><a href="#">Contact</a>
</nav>
<div class="abs phone">
  <svg width="40" height="40" viewBox="0 0 40 40"><circle cx="20" cy="20" r="18" fill="none" stroke="#1c5bb4" stroke-width="2.5"/><path d="M14 11l4 0 2 5-3 2q2 4 6 6l2-3 5 2 0 4q-1 2-3 2-14-2-16-16 0-2 3-2z" fill="#1c5bb4"/></svg>
  (555)014 2368
</div>
<div class="abs brand hero-title">BRIGHTMOOR LIFT INC</div>
<div class="abs tagline">Lorem ipsum dolor sitectetur adipiscing elit</div>
<div class="abs btn btn-hero">GET FREE QUOTE <svg width="16" height="16" viewBox="0 0 16 16"><circle cx="8" cy="8" r="8" fill="#fff"/><path d="M6 4l4 4-4 4" stroke="#1c5bb4" stroke-width="2.2" fill="none"/></svg></div>
<div class="abs dots"><span></span><span></span><span class="on"></span><span></span><span></span></div>

<!-- about -->
<div class="abs about-ring"></div>
<div class="abs about-photo" role="img" aria-label="City skyline of tall office towers in a circular frame"></div>
<div class="abs about-inner"></div>
<div class="abs cond about-h1">ABOUT</div>
<div class="abs cond about-h2">BRIGHTMOOR</div>
<div class="abs cond about-h3">LIFT INC</div>

<!-- services -->
<div class="abs services-band" role="img" aria-label="Blue tinted city skyline behind the services section"></div>
<svg class="abs services-svg" width="1200" height="140" viewBox="0 0 1200 140">
  <path d="M0 0 L1200 0 L1200 2 Q600 260 0 2Z" fill="#ffffff"/>
</svg>
<p class="abs about-p">Lorem ipsum dolor sit amet, consectetur adipiscing elit, sed do eiusmod tempor incididunt ut labore et dolore magna aliqua. Quis ipsum suspendisse ultrices gravida. Risus commodo viverra maecenas accumsan lacus vel facilisis.rem ipsum dolor sit amet, consectetur adipiscing elit, sed do eiusmod tempor incididunt ut labore et dolore magna aliqua. Quis ipsum suspendisse ultrices gravida. Risus commodo viverra maecenas.</p>
<div class="abs section-title services-title">OUR SERVICES</div>

<div class="abs card" style="left:144px">
  <div class="card-img" role="img" aria-label="Escalator in a modern building" style="background:linear-gradient(135deg,#c9b9a6,#6f6a66 60%,#2c2c2e)"></div>
  <h3>MODERNIZATION</h3>
  <p>Lorem ipsum dolor sit amet, consectetur adipiscing elit sed do eiusmod tempor incididunt</p>
  <div class="btn">READ MORE <svg width="13" height="13" viewBox="0 0 16 16"><circle cx="8" cy="8" r="8" fill="#fff"/><path d="M6 4l4 4-4 4" stroke="#1c5bb4" stroke-width="2.2" fill="none"/></svg></div>
</div>
<div class="abs card" style="left:453px">
  <div class="card-img" role="img" aria-label="Red lit elevator shaft viewed from below" style="background:radial-gradient(circle,#e8a18c,#8c2018 45%,#2a0b0a)"></div>
  <h3>MAINTENANCE</h3>
  <p>Lorem ipsum dolor sit amet, consectetur adipiscing elit sed do eiusmod tempor incididunt</p>
  <div class="btn">READ MORE <svg width="13" height="13" viewBox="0 0 16 16"><circle cx="8" cy="8" r="8" fill="#fff"/><path d="M6 4l4 4-4 4" stroke="#1c5bb4" stroke-width="2.2" fill="none"/></svg></div>
</div>
<div class="abs card" style="left:762px">
  <div class="card-img" role="img" aria-label="Technician servicing an elevator shaft" style="background:linear-gradient(135deg,#9aa3ad,#56606c 55%,#2d343c)"></div>
  <h3>SERVICE &amp; REPAIR</h3>
  <p>Lorem ipsum dolor sit amet, consectetur adipiscing elit sed do eiusmod tempor incididunt</p>
  <div class="btn">READ MORE <svg width="13" height="13" viewBox="0 0 16 16"><circle cx="8" cy="8" r="8" fill="#fff"/><path d="M6 4l4 4-4 4" stroke="#1c5bb4" stroke-width="2.2" fill="none"/></svg></div>
</div>

<!-- gallery -->
<div class="abs section-title gallery-title"><span>PHOTO</span> GALLERY</div>
<div class="abs" role="img" aria-label="Open elevator door in a bright lobby" style="left:144px;top:2178px;width:297px;height:421px;background:linear-gradient(90deg,#6b6f78,#c7c9cd 45%,#e9eaec)"></div>
<div class="abs" role="img" aria-label="Row of elevator doors in a lobby" style="left:451px;top:2178px;width:297px;height:208px;background:linear-gradient(180deg,#bfc3c8,#6c7179 55%,#c9ccd0)"></div>
<div class="abs" role="img" aria-label="Technician working on top of an elevator car" style="left:451px;top:2393px;width:297px;height:206px;background:linear-gradient(135deg,#a6a8aa,#6d6f72 50%,#3b3d40)"></div>
<div class="abs" role="img" aria-label="Neon lit elevator shaft in pink and teal" style="left:758px;top:2178px;width:298px;height:421px;background:radial-gradient(circle at 50% 40%,#f2c8e4,#9a3a8a 30%,#10415a 65%,#071a24)"></div>
<div class="abs" role="img" aria-label="Glass elevator shaft inside an atrium" style="left:144px;top:2608px;width:297px;height:206px;background:linear-gradient(135deg,#d2dbe2,#7d8995 50%,#3c4550)"></div>
<div class="abs" role="img" aria-label="Interior of a steel elevator cab" style="left:451px;top:2608px;width:297px;height:206px;background:linear-gradient(90deg,#55595e,#c5c8cc 50%,#55595e)"></div>
<div class="abs" role="img" aria-label="Technician inside an elevator shaft" style="left:758px;top:2608px;width:298px;height:206px;background:linear-gradient(135deg,#b7ab98,#6f6a60 55%,#36332f)"></div>

<!-- quote -->
<div class="abs quote-band" role="img" aria-label="Dark view up an elevator shaft"></div>
<svg class="abs quote-svg" width="1200" height="130" viewBox="0 0 1200 130">
  <path d="M0 0 L1200 0 L1200 10 Q600 220 0 10Z" fill="#ffffff"/>
  <path d="M130 50 Q600 170 1200 10" fill="none" stroke="#1c5bb4" stroke-width="9"/>
</svg>
<div class="abs section-title quote-title"><span>GET</span> FREE QUOTE</div>
<div class="abs field" style="left:144px;top:3220px;width:266px;height:48px">Enter Name</div>
<div class="abs field" style="left:424px;top:3220px;width:266px;height:48px">Enter Email</div>
<div class="abs field" style="left:144px;top:3285px;width:266px;height:48px">Phone</div>
<div class="abs field" style="left:424px;top:3285px;width:266px;height:48px">Address</div>
<div class="abs field" style="left:144px;top:3350px;width:266px;height:48px">Your City</div>
<div class="abs field" style="left:424px;top:3350px;width:266px;height:48px">Problem/Issues</div>
<div class="abs field" style="left:705px;top:3220px;width:351px;height:178px">Message</div>
<div class="abs btn btn-submit">SUBMIT MESSAGE <svg width="16" height="16" viewBox="0 0 16 16"><circle cx="8" cy="8" r="8" fill="#fff"/><path d="M6 4l4 4-4 4" stroke="#1c5bb4" stroke-width="2.2" fill="none"/></svg></div>

<!-- contact -->
<div class="abs contact" style="left:65px;top:3664px">
  <div class="c-icon"><svg width="26" height="26" viewBox="0 0 40 40"><path d="M10 5l7 0 3 8-5 3q3 7 9 9l3-5 8 3 0 7q-1 4-5 4-22-3-25-25 0-4 5-4z" fill="#1c5bb4"/></svg></div>
  <h4>PHONE</h4><p>(+428) 888 888 8888</p>
</div>
<div class="abs contact" style="left:291px;top:3664px">
  <div class="c-icon"><svg width="22" height="28" viewBox="0 0 22 28"><path d="M11 1C5 1 1 5 1 11c0 7 10 16 10 16s10-9 10-16C21 5 17 1 11 1z" fill="#1c5bb4"/><circle cx="11" cy="11" r="4" fill="#fff"/></svg></div>
  <h4>HEAD OFFICE</h4><p>123 west Dummy Car Street, Old City,<br>New State, USA. PO 4288</p>
</div>
<div class="abs contact" style="left:569px;top:3664px">
  <div class="c-icon fill"><svg width="22" height="28" viewBox="0 0 22 28"><path d="M11 1C5 1 1 5 1 11c0 7 10 16 10 16s10-9 10-16C21 5 17 1 11 1z" fill="#fff"/><circle cx="11" cy="11" r="4" fill="#1c5bb4"/></svg></div>
  <h4>MAIN OFFICE</h4><p>123 west Dummy Car Street, Old City,<br>New State, USA. PO 4288</p>
</div>
<div class="abs contact" style="left:818px;top:3664px">
  <div class="c-icon"><svg width="28" height="20" viewBox="0 0 28 20"><rect x="0" y="0" width="28" height="20" rx="2" fill="#1c5bb4"/><path d="M1 2l13 9 13-9" stroke="#fff" stroke-width="2" fill="none"/></svg></div>
  <h4>EMAIL</h4><p>info@companyname.com</p>
</div>

<!-- footer -->
<div class="abs rule"></div>
<div class="abs copy">© Copyright &nbsp;2020 Brightmoor Lift. All Rights Reserved | Terms and Conditions | Privacy Policy</div>
<div class="abs social" style="left:918px"></div>
<div class="abs social" style="left:965px"></div>
<div class="abs social" style="left:1014px"></div>
<div class="abs foot-bar"></div>

</body>
</html>
```